New Dental Office Needs an Attractive and user friendly Website Designed

I need a website for a new dental office. The Name is Harrowfield Dentistry. I would like a Modern design with a user friendly interface and usability.
I would like a landing page, a page that lists the services we offer: Cosmetic Dentistry, Implants, Dental Hygiene, Emergency Services, Restorations, Dentures
Target Market(s)
Mid to upper class
Industry/Entity Type
Dentistry
Coding
Number of Pages Required
1 page
Requirements
Must have
- Landing page that has a scheduling option, Procedures, operating hours, and contact us info
Nice to have
- Appealing design, Soft comforting colors. Easy to navigate page, Modern and professional.

```html
<!DOCTYPE html>
<html lang="en">
<head>
<meta charset="utf-8">
<title>Harrowfield Dentistry</title>
<link href="https://fonts.googleapis.com/css2?family=Josefin+Sans:wght@300;400;600&family=Montserrat:wght@400;500;600&display=swap" rel="stylesheet">
<style>
:root{
  --blue:#1e8fd6;
  --blue-light:#5bbde6;
  --nav-bg:#e3f1f9;
  --ink:#1f2329;
  --body:#3a3f45;
  --grey-bg:#eeeff1;
  --card:#ffffff;
  --footer:#2a2a2c;
  --footer-text:#e6e6e6;
}
*{box-sizing:border-box;margin:0;padding:0}
html,body{width:1200px;height:4640px;overflow:hidden;background:#fff}
body{position:relative;font-family:"Montserrat",sans-serif;color:var(--body)}
.abs{position:absolute}
.heading{font-family:"Josefin Sans",sans-serif;font-weight:400;color:var(--ink);letter-spacing:1px}
.btn{position:absolute;display:flex;align-items:center;justify-content:center;background:var(--blue);color:#fff;border-radius:40px;font-family:"Josefin Sans",sans-serif;font-size:19px;letter-spacing:1px}
.photo{position:absolute;overflow:hidden}
.small-text{font-size:12.5px;line-height:25px;color:var(--body)}

/* header */
.topbar{position:absolute;left:0;top:0;width:1200px;height:81px;background:#fff}
.call-icon{left:73px;top:18px;width:46px;height:46px;border-radius:50%;background:var(--blue)}
.call-label{left:131px;top:20px;font-size:12px;font-weight:600;color:var(--blue)}
.call-numbers{left:131px;top:38px;font-size:18px;font-weight:600;color:var(--ink);letter-spacing:.5px}
.brand-name{position:absolute;font-family:"Josefin Sans",sans-serif;font-weight:400;text-align:center;white-space:nowrap}
.brand-top{left:420px;top:25px;width:360px;font-size:30px;line-height:34px;color:#2d2d2d}
.nav{position:absolute;left:0;top:81px;width:1200px;height:50px;background:var(--nav-bg)}
.nav a{position:absolute;top:16px;transform:translateX(-50%);font-family:"Josefin Sans",sans-serif;font-size:18px;color:var(--ink);text-decoration:none;white-space:nowrap}
.nav a.active{color:var(--blue)}
.nav a.active::after{content:"";position:absolute;left:-12px;right:-12px;bottom:-16px;height:3px;background:var(--blue)}

/* hero */
.hero{left:0;top:131px;width:1200px;height:616px;background:linear-gradient(90deg,#e9eef2 0%,#dfe7ec 45%,#c9d6df 100%)}
.hero-title{left:74px;top:262px;font-size:72px;line-height:66px}
.hero-sub{left:76px;top:405px;font-size:40px;line-height:42px}
.dots{left:74px;top:637px}
.dots span{display:inline-block;width:12px;height:12px;border-radius:50%;background:#111;margin-right:8px}
.dots span:first-child{background:var(--blue)}

/* welcome */
.welcome-title{left:616px;top:864px;font-size:36px;line-height:41px}
.welcome-text{left:616px;top:984px;width:520px}

/* services */
.services-bg{left:0;top:1377px;width:1200px;height:972px;background:var(--grey-bg)}
.section-title{font-size:36px;line-height:40px}
.title-rule{position:absolute;height:3px;width:100px;background:var(--blue)}
.card{position:absolute;width:241px;height:322px;background:var(--card);border-radius:8px;overflow:hidden}
.card.featured{border:3px solid var(--blue)}
.card .card-photo{position:absolute;left:0;top:0;width:100%;height:175px}
.card .card-icon{position:absolute;left:40px;top:128px;width:52px;height:52px;border-radius:50%;background:#fff;border:2px solid var(--blue)}
.card h3{position:absolute;left:15px;top:206px;font-family:"Josefin Sans",sans-serif;font-weight:400;font-size:20px;color:var(--blue);letter-spacing:.5px}
.card p{position:absolute;left:15px;top:236px;width:215px;font-size:12.5px;line-height:23px;color:var(--body)}

/* procedures */
.proc-item h4{font-family:"Josefin Sans",sans-serif;font-weight:400;font-size:21px;color:var(--blue)}
.tick{position:absolute;width:32px;height:32px}

/* testimonials */
.testi-bg{left:0;top:2952px;width:1200px;height:603px;background:var(--grey-bg)}
.testi-card{left:254px;top:3188px;width:689px;height:214px;background:#fff;border-radius:4px}

/* form */
.field{position:absolute;height:54px;border:1px solid #b9bcc0;border-radius:30px;padding:0 22px;display:flex;align-items:center;font-size:13px;color:var(--ink);background:#fff}

/* footer */
.footer{left:0;top:4180px;width:1200px;height:460px;background:var(--footer)}
.foot-head{font-family:"Josefin Sans",sans-serif;font-size:25px;color:var(--blue);letter-spacing:1px}
.foot-list{font-size:15px;color:var(--footer-text);line-height:34px}
</style>
</head>
<body>

<!-- header -->
<header class="topbar">
  <div class="abs call-icon"></div>
  <svg class="abs" style="left:85px;top:30px" width="22" height="22" viewBox="0 0 24 24"><path fill="#fff" d="M6.6 10.8a15.1 15.1 0 0 0 6.6 6.6l2.2-2.2c.3-.3.7-.4 1-.2 1.1.4 2.3.6 3.6.6.6 0 1 .4 1 1V20c0 .6-.4 1-1 1A17 17 0 0 1 3 4c0-.6.4-1 1-1h3.5c.6 0 1 .4 1 1 0 1.3.2 2.5.6 3.6.1.3 0 .7-.2 1z"/></svg>
  <div class="abs call-label">CALL US</div>
  <div class="abs call-numbers">(555) 014-2280,&nbsp; (555) 017-3940</div>
  <div class="brand-name brand-top">Harrowfield Dentistry</div>
  <div class="btn" style="left:871px;top:18px;width:254px;height:45px">Book an Appointment</div>
</header>

<nav class="nav">
  <a class="active" style="left:164px">Home</a>
  <a style="left:270px">About</a>
  <a style="left:385px">Services</a>
  <a style="left:529px">Testimonials</a>
  <a style="left:673px">Specials</a>
  <a style="left:850px">Patient Information</a>
  <a style="left:1023px">Contact</a>
</nav>

<!-- hero -->
<section class="photo hero" role="img" aria-label="Smiling patient in a dental chair giving a thumbs up, dentist working in the background"></section>
<h1 class="abs heading hero-title">Harrowfield<br>Dentistry</h1>
<p class="abs heading hero-sub">Dental Care You Can<br>Count On</p>
<div class="btn" style="left:74px;top:515px;width:250px;height:57px">Book an Appointment</div>
<div class="abs dots"><span></span><span></span><span></span><span></span></div>
<svg class="abs" style="left:0;top:640px" width="1200" height="120" viewBox="0 0 1200 120">
  <path d="M0 60 C300 130 700 70 900 40 C1050 20 1150 30 1200 40 L1200 120 L0 120 Z" fill="#fff"/>
  <path d="M0 60 C300 130 700 70 900 40 C1050 20 1150 30 1200 40" fill="none" stroke="var(--blue-light)" stroke-width="9"/>
</svg>
<svg class="abs" style="left:554px;top:674px" width="92" height="92" viewBox="0 0 92 92" aria-label="Scroll down">
  <circle cx="46" cy="46" r="44" fill="#d7ecf7"/>
  <circle cx="46" cy="46" r="22" fill="#fff"/>
  <path d="M46 35 V56 M38 49 L46 57 L54 49" stroke="#111" stroke-width="3" fill="none"/>
</svg>

<!-- welcome -->
<svg class="abs" style="left:95px;top:855px" width="400" height="400" viewBox="0 0 400 400"><path d="M30 260 A190 190 0 0 1 300 40" fill="none" stroke="var(--blue-light)" stroke-width="8"/></svg>
<div class="photo" style="left:107px;top:872px;width:380px;height:380px;border-radius:50%;background:linear-gradient(135deg,#7f8b95,#b9c3ca 50%,#8fd0d8)" role="img" aria-label="Dentist and assistant treating a patient"></div>
<div class="photo" style="left:365px;top:1076px;width:206px;height:206px;border-radius:50%;border:4px solid #fff;background:linear-gradient(180deg,#bcd7ea,#e9e4dc 55%,#8a6a58)" role="img" aria-label="Front of the dental office building"></div>
<div class="abs" style="left:102px;top:888px;width:96px;height:96px;border-radius:50%;background:#e9b85a;border:4px solid #fff" role="img" aria-label="Practice badge"></div>
<h2 class="abs heading welcome-title">Welcome to<br>Harrowfield Dentistry</h2>
<div class="abs welcome-text small-text">
  <p>Welcome to Harrowfield Family Dentistry. Born in this area,<br>Dr. Owen Maddox has always had a desire to return to Larkin County. Today<br>he is pleased to offer high-quality dental care to friends and neighbors in<br>Larkin Falls. He believes in giving back and is an engaged member of<br>our community.</p>
  <p style="margin-top:8px">Dr. Maddox partners with his patients because your input matters to us.<br>Our job is to listen to you, respect your feelings and concerns, and provide<br>information and education instead of words of judgment.</p>
</div>
<div class="btn" style="left:616px;top:1220px;width:250px;height:58px">Book an Appointment</div>

<!-- services -->
<section class="abs services-bg"></section>
<svg class="abs" style="left:0;top:1360px" width="1200" height="110" viewBox="0 0 1200 110">
  <path d="M0 0 H1200 V50 C1100 80 950 60 800 40 C600 10 350 70 0 40 Z" fill="#fff"/>
  <path d="M0 40 C350 -10 600 30 800 40 C950 50 1100 80 1200 50" fill="none" stroke="var(--blue-light)" stroke-width="9"/>
</svg>
<h2 class="abs heading section-title" style="left:74px;top:1527px">Services We<br>Offer</h2>
<div class="title-rule" style="left:74px;top:1617px;width:90px"></div>
<p class="abs small-text" style="left:74px;top:1642px;width:270px">If you're looking for a wide array of dental services for your family, Harrowfield Dentistry offers everything you need.</p>
<div class="btn" style="left:76px;top:1769px;width:221px;height:56px">View All Services</div>

<div class="card" style="left:373px;top:1532px"><div class="photo card-photo" style="background:linear-gradient(135deg,#c9b9a8,#efe8e1)" role="img" aria-label="Smiling man holding a tooth shade guide"></div><div class="card-icon"></div><h3>Cosmetic Dentistry</h3><p>Duis aute irure dolor in reprehenderit in voluptate velit enim ipsam voluptat.</p></div>
<div class="card featured" style="left:628px;top:1532px;width:245px"><div class="photo card-photo" style="background:linear-gradient(135deg,#d9a7a0,#f1e4e2)" role="img" aria-label="Dental implant model in gloved hands"></div><div class="card-icon"></div><h3>Implants</h3><p>Duis aute irure dolor in reprehenderit in voluptate velit enim ipsam voluptat.</p></div>
<div class="card" style="left:884px;top:1532px"><div class="photo card-photo" style="background:linear-gradient(135deg,#6b5b52,#dcd9d6)" role="img" aria-label="Couple brushing their teeth"></div><div class="card-icon"></div><h3>Dental Hygiene</h3><p>Duis aute irure dolor in reprehenderit in voluptate velit enim ipsam voluptat.</p></div>
<div class="card" style="left:74px;top:1874px"><div class="photo card-photo" style="background:linear-gradient(135deg,#bfa08c,#f3efec)" role="img" aria-label="Man holding his jaw in pain"></div><div class="card-icon"></div><h3>Emergency Services</h3><p>Duis aute irure dolor in reprehenderit in voluptate velit enim ipsam voluptat.</p></div>
<div class="card" style="left:331px;top:1874px"><div class="photo card-photo" style="background:linear-gradient(180deg,#b5393f,#f2f2f2 60%,#b5393f)" role="img" aria-label="Close-up of white teeth"></div><div class="card-icon"></div><h3>Restorations</h3><p>Duis aute irure dolor in reprehenderit in voluptate velit enim ipsam voluptat.</p></div>
<div class="card" style="left:587px;top:1874px"><div class="photo card-photo" style="background:linear-gradient(135deg,#f2f2f2,#e0727a)" role="img" aria-label="Set of dentures"></div><div class="card-icon"></div><h3>Dentures</h3><p>Duis aute irure dolor in reprehenderit in voluptate velit enim ipsam voluptat.</p></div>
<div class="photo" style="left:925px;top:1990px;width:180px;height:320px;border-radius:40px 40px 20px 20px;background:linear-gradient(90deg,#e6e0d4,#faf8f3)" role="img" aria-label="Tooth-shaped holder with dental instruments"></div>
<svg class="abs" style="left:0;top:2260px" width="1200" height="110" viewBox="0 0 1200 110">
  <path d="M0 40 C250 80 600 90 900 70 C1050 60 1150 40 1200 20 V110 H0 Z" fill="#fff"/>
  <path d="M0 40 C250 80 600 90 900 70 C1050 60 1150 40 1200 20" fill="none" stroke="var(--blue-light)" stroke-width="9"/>
</svg>

<!-- procedures -->
<h2 class="abs heading section-title" style="left:74px;top:2430px">Our Procedures</h2>
<div class="title-rule" style="left:74px;top:2475px;width:90px"></div>
<p class="abs small-text" style="left:74px;top:2500px;width:510px">We know that the best dental care combines training, skill, experience, compassion, and personal connection. But for us to help you achieve your oral health goals, we know we must be the kind of people you feel you can trust to take care of your smile.</p>

<svg class="tick" style="left:74px;top:2622px" viewBox="0 0 32 32"><circle cx="16" cy="16" r="14" fill="none" stroke="var(--blue)" stroke-width="2.5"/><path d="M9 16 L14 21 L23 11" fill="none" stroke="var(--blue)" stroke-width="3"/></svg>
<div class="abs proc-item" style="left:121px;top:2613px;width:470px"><h4>Calm</h4><p class="small-text">Going to the dentist can be a stressful experience. We take the time to listen to your concerns</p></div>
<svg class="tick" style="left:74px;top:2707px" viewBox="0 0 32 32"><circle cx="16" cy="16" r="14" fill="none" stroke="var(--blue)" stroke-width="2.5"/><path d="M9 16 L14 21 L23 11" fill="none" stroke="var(--blue)" stroke-width="3"/></svg>
<div class="abs proc-item" style="left:121px;top:2698px;width:470px"><h4>Comfortable</h4><p class="small-text">We use tools and products that are designed to improve your comfort. Two of the biggest complaints of the dentist.</p></div>
<svg class="tick" style="left:74px;top:2797px" viewBox="0 0 32 32"><circle cx="16" cy="16" r="14" fill="none" stroke="var(--blue)" stroke-width="2.5"/><path d="M9 16 L14 21 L23 11" fill="none" stroke="var(--blue)" stroke-width="3"/></svg>
<div class="abs proc-item" style="left:121px;top:2788px;width:470px"><h4>Clean</h4><p class="small-text">There is a lot that goes on behind the scenes before and after your dental appointment.</p></div>

<svg class="abs" style="left:720px;top:2420px" width="420" height="420" viewBox="0 0 420 420"><path d="M60 40 A200 200 0 0 1 400 230" fill="none" stroke="var(--blue-light)" stroke-width="8"/></svg>
<div class="photo" style="left:747px;top:2448px;width:378px;height:378px;border-radius:50%;background:linear-gradient(135deg,#9aa7b2,#dfe6ea 50%,#6f9fc4)" role="img" aria-label="Dentist reviewing an x-ray with a patient"></div>
<div class="photo" style="left:649px;top:2651px;width:206px;height:206px;border-radius:50%;border:4px solid #fff;background:linear-gradient(135deg,#6e4a3a,#d8dde2)" role="img" aria-label="Patient having a dental check-up"></div>

<!-- testimonials -->
<section class="abs testi-bg"></section>
<svg class="abs" style="left:0;top:2930px" width="1200" height="80" viewBox="0 0 1200 80">
  <path d="M0 0 H1200 V20 C1000 0 800 10 600 40 C400 60 200 40 0 50 Z" fill="#fff"/>
  <path d="M0 50 C200 40 400 60 600 40 C800 10 1000 0 1200 20" fill="none" stroke="var(--blue-light)" stroke-width="9"/>
</svg>
<h2 class="abs heading section-title" style="left:0;top:3090px;width:1200px;text-align:center;font-size:34px">What Our Patients Say About Us</h2>
<div class="title-rule" style="left:524px;top:3144px;width:152px"></div>
<div class="abs testi-card"></div>
<div class="photo" style="left:283px;top:3208px;width:176px;height:176px;border-radius:50%;background:linear-gradient(135deg,#c9dbe6,#8a6452)" role="img" aria-label="Portrait of a smiling patient"></div>
<div class="abs" style="left:488px;top:3212px;color:#f19a1b;font-size:24px;letter-spacing:3px">★★★★★</div>
<p class="abs small-text" style="left:488px;top:3243px;width:420px">" Duis aute irure dolor in reprehenderit in voluptate velit esse cillum dolore eu fugiat nulla pariatur. Excepteur sint occaecat cupidatat non proident, sunt in culpa qui officia deserunt mollit anim id est laborum...."</p>
<div class="abs heading" style="left:488px;top:3350px;font-size:18px;color:var(--blue)">Name Heading</div>
<svg class="abs" style="left:195px;top:3278px" width="32" height="32" viewBox="0 0 32 32"><circle cx="16" cy="16" r="13" fill="none" stroke="#666" stroke-width="2.5"/><path d="M19 10 L13 16 L19 22" fill="none" stroke="#666" stroke-width="3"/></svg>
<svg class="abs" style="left:972px;top:3278px" width="32" height="32" viewBox="0 0 32 32"><circle cx="16" cy="16" r="13" fill="none" stroke="var(--blue)" stroke-width="2.5"/><path d="M13 10 L19 16 L13 22" fill="none" stroke="var(--blue)" stroke-width="3"/></svg>
<svg class="abs" style="left:0;top:3490px" width="1200" height="80" viewBox="0 0 1200 80">
  <path d="M0 20 C250 0 500 50 800 60 C1000 66 1120 40 1200 30 V80 H0 Z" fill="#fff"/>
  <path d="M0 20 C250 0 500 50 800 60 C1000 66 1120 40 1200 30" fill="none" stroke="var(--blue-light)" stroke-width="9"/>
</svg>

<!-- appointment -->
<h2 class="abs heading section-title" style="left:0;top:3624px;width:1200px;text-align:center;font-size:34px">Book An Appointment</h2>
<div class="title-rule" style="left:524px;top:3678px;width:152px"></div>
<div class="field" style="left:164px;top:3721px;width:423px">Full Name</div>
<div class="field" style="left:614px;top:3721px;width:425px">Email Address</div>
<div class="field" style="left:164px;top:3789px;width:423px">Phone No</div>
<div class="field" style="left:614px;top:3789px;width:425px;justify-content:space-between">Select Services<span style="font-size:10px;line-height:10px">▲<br>▼</span></div>
<div class="field" style="left:164px;top:3856px;width:875px;height:122px;align-items:flex-start;padding-top:22px;border-radius:40px">Message</div>
<div class="btn" style="left:488px;top:3998px;width:223px;height:57px">Submit</div>

<!-- footer -->
<section class="abs footer"></section>
<svg class="abs" style="left:0;top:4120px" width="1200" height="90" viewBox="0 0 1200 90">
  <path d="M0 20 C300 60 600 80 900 50 C1050 35 1150 10 1200 0 V90 H0 Z" fill="var(--footer)"/>
  <path d="M0 20 C300 60 600 80 900 50 C1050 35 1150 10 1200 0" fill="none" stroke="var(--blue-light)" stroke-width="9"/>
</svg>
<div class="brand-name" style="left:49px;top:4310px;width:280px;color:#fff;font-size:30px;line-height:34px">Harrowfield<br>Dentistry</div>
<div class="abs" style="left:100px;top:4400px;display:flex;gap:18px">
  <span style="width:16px;height:16px;border-radius:50%;background:#fff" aria-label="Social link"></span>
  <span style="width:16px;height:16px;border-radius:50%;background:var(--blue)" aria-label="Social link"></span>
  <span style="width:16px;height:16px;border-radius:50%;background:#fff" aria-label="Social link"></span>
  <span style="width:16px;height:16px;border-radius:50%;background:#fff" aria-label="Social link"></span>
  <span style="width:16px;height:16px;border-radius:50%;background:#fff" aria-label="Social link"></span>
</div>
<p class="abs" style="left:64px;top:4446px;width:250px;text-align:center;font-size:11.5px;line-height:24px;color:var(--footer-text)">Copyright © 2025. Company Name.<br>All Right Reserved</p>

<div class="abs foot-head" style="left:353px;top:4290px">Quick Links</div>
<div class="abs foot-list" style="left:353px;top:4330px">Home<br>About<br>Services<br>Testimonials<br>Specials<br>Patient Information<br>Contact</div>

<div class="abs foot-head" style="left:594px;top:4290px">Contact Info</div>
<div class="abs foot-list" style="left:594px;top:4330px;line-height:29px">
  <div style="display:flex;gap:12px"><svg width="16" height="29" viewBox="0 0 16 16"><path d="M1 4 L5 2 L11 4 L15 2 V12 L11 14 L5 12 L1 14 Z" fill="var(--blue)"/></svg><span>48 Meadow Lane<br>Larkin Falls, IA 50000</span></div>
  <div style="display:flex;gap:12px;margin-top:11px"><svg width="16" height="29" viewBox="0 0 24 24"><path fill="var(--blue)" d="M6.6 10.8a15.1 15.1 0 0 0 6.6 6.6l2.2-2.2c.3-.3.7-.4 1-.2 1.1.4 2.3.6 3.6.6.6 0 1 .4 1 1V20c0 .6-.4 1-1 1A17 17 0 0 1 3 4c0-.6.4-1 1-1h3.5c.6 0 1 .4 1 1 0 1.3.2 2.5.6 3.6.1.3 0 .7-.2 1z"/></svg><span>(555) 019-4410</span></div>
  <div style="display:flex;gap:12px;margin-top:11px"><svg width="16" height="29" viewBox="0 0 16 16"><rect x="2" y="5" width="12" height="9" fill="var(--blue)"/><rect x="4" y="1" width="8" height="4" fill="var(--blue)"/></svg><span>(555) 019-4420</span></div>
  <div style="display:flex;gap:12px;margin-top:11px"><svg width="16" height="29" viewBox="0 0 16 16"><rect x="1" y="3" width="14" height="10" fill="var(--blue)"/><path d="M1 3 L8 9 L15 3" stroke="#fff" fill="none"/></svg><span>hello@harrowfielddental.com</span></div>
</div>

<div class="abs foot-head" style="left:900px;top:4290px">Hours</div>
<div class="abs foot-list" style="left:900px;top:4330px;line-height:40px">Mon<br>Tue<br>Wed<br>Fri</div>
<div class="abs foot-list" style="left:1008px;top:4330px;line-height:40px">7:30AM - 4:30PM<br>7:30AM - 4:30PM<br>7:30AM - 4:30PM<br>7:30AM - 3:00PM</div>

</body>
</html>
```